Oil and Gas Exploration and Production company needs a business card design

We need a business card design using our logo and colors in the logo. We want a mainstream design.

```html
<!DOCTYPE html>
<html lang="en">
<head>
<meta charset="utf-8">
<title>Ridgeline Oil &amp; Gas – Business Card</title>
<link rel="stylesheet" href="https://fonts.googleapis.com/css2?family=Roboto+Slab:wght@400;700&family=Roboto:wght@400;500&display=swap">
<style>
  :root {
    --bg: #5e4a32;
    --ink: #151515;
    --paper: #ffffff;
    --gold: #c89a2c;
    --gold-deep: #b8891f;
    --text-light: #f2f2f2;
  }
  * { margin: 0; padding: 0; box-sizing: border-box; }
  html, body { width: 1200px; height: 911px; overflow: hidden; }
  body { background: var(--bg); position: relative; font-family: "Roboto", Arial, sans-serif; }

  .card {
    position: absolute;
    width: 540px;
    height: 310px;
    border-radius: 22px;
    overflow: hidden;
    box-shadow: 0 10px 24px rgba(0,0,0,0.35);
  }
  .card-front { left: 80px; top: 110px; background: var(--ink); }
  .card-back { left: 580px; top: 490px; background: var(--gold); }

  .front-shape { position: absolute; inset: 0; }

  .holder { position: absolute; left: 36px; top: 40px; }
  .holder-name {
    font-family: "Roboto Slab", Georgia, serif;
    font-weight: 700; font-size: 24px; color: var(--gold);
  }
  .holder-title { font-size: 15px; color: var(--text-light); margin-top: 2px; }

  .contact-list {
    position: absolute; left: 36px; bottom: 26px;
    list-style: none; color: var(--text-light); font-size: 13.5px; line-height: 20px;
  }
  .contact-list li { display: flex; align-items: center; gap: 9px; }
  .contact-list .address { display: block; padding-left: 23px; margin-bottom: 2px; }
  .contact-icon { width: 14px; height: 14px; flex: none; fill: var(--gold); }

  .brand {
    position: absolute; right: 34px; top: 48px;
    display: flex; align-items: center; gap: 12px;
  }
  .brand-dot { width: 30px; height: 30px; border-radius: 50%; background: var(--ink); flex: none; }
  .brand-name {
    font-family: "Roboto Slab", Georgia, serif;
    font-weight: 700; font-size: 34px; line-height: 36px; color: var(--ink);
  }

  .back-brand {
    position: absolute; left: 50%; top: 50%; transform: translate(-50%, -50%);
    display: flex; align-items: center; gap: 14px;
  }
  .back-brand .brand-dot { width: 56px; height: 56px; }
  .back-brand .brand-name { font-size: 32px; }

  .back-web {
    position: absolute; left: 36px; bottom: 28px;
    font-size: 13px; letter-spacing: 5px; color: var(--paper);
  }
</style>
</head>
<body>

<section class="card card-front" aria-label="Business card front">
  <svg class="front-shape" viewBox="0 0 540 310" preserveAspectRatio="none" aria-hidden="true">
    <path d="M238 0 C 300 130, 390 235, 540 258 L540 0 Z" fill="var(--paper)"/>
    <path d="M238 0 C 300 130, 390 235, 540 258" fill="none" stroke="var(--gold)" stroke-width="7" transform="translate(-6,8)"/>
    <path d="M238 0 C 300 130, 390 235, 540 258 L540 0 Z" fill="var(--paper)"/>
  </svg>

  <div class="holder">
    <p class="holder-name">Daniel Harper</p>
    <p class="holder-title">CEO/Founder</p>
  </div>

  <ul class="contact-list">
    <li class="address">1420 Cedar Hollow Road<br>Fairbanks, Alaska 99701</li>
    <li><svg class="contact-icon" viewBox="0 0 16 16"><path d="M3 1l3 3-2 2c1 2 3 4 5 5l2-2 3 3-2 3C7 15 1 9 0 4z"/></svg>907 214 5530</li>
    <li><svg class="contact-icon" viewBox="0 0 16 16"><rect x="4" y="0" width="8" height="16" rx="2"/></svg>907 388 1642</li>
    <li><svg class="contact-icon" viewBox="0 0 16 16"><rect x="1" y="5" width="14" height="10" rx="1"/><rect x="4" y="1" width="8" height="5"/></svg>907 551 2087</li>
    <li><svg class="contact-icon" viewBox="0 0 16 16"><path d="M0 3h16v10H0z M0 3l8 6 8-6" stroke="var(--ink)" stroke-width="1"/></svg>info@ridgelineog.com</li>
    <li><svg class="contact-icon" viewBox="0 0 16 16"><circle cx="8" cy="8" r="8"/><path d="M0 8h16M8 0v16" stroke="var(--ink)" stroke-width="1.2"/></svg>www.ridgelineog.com</li>
  </ul>

  <div class="brand">
    <span class="brand-dot"></span>
    <p class="brand-name">Ridgeline<br>Oil &amp; Gas</p>
  </div>
</section>

<section class="card card-back" aria-label="Business card back">
  <div class="back-brand">
    <span class="brand-dot"></span>
    <p class="brand-name">Ridgeline Oil &amp; Gas</p>
  </div>
  <p class="back-web">www.ridgelineog.com</p>
</section>

</body>
</html>
```